Local Flower Farm Needs Business Card Design

I need business cards designed for a flower farm based in Eudora, Kansas.
Business Info:
We are a local cut flower farm located in Eudora, Kansas, founded by Corinne Haldwick. What started as a passion for agriculture and search for more joy in daily life has blossomed into a small business dedicated to providing the community with beautiful, fresh, and sustainable flowers. We specialize in local, seasonal blooms, ensuring that every petal reflects the care and dedication we pour into our craft. Our mission is to deliver the highest quality flowers directly to our customers through local farmers markets and to florists who share our commitment to sustainability. Join us in celebrating the beauty of nature, one bloom at a time!
Contact Details:
Corinne Haldwick
Owner
Phone 913-555-0147
Facebook: Rosalind Thorpe Gardens
Instagram: @RosalindThorpeGardens
Website: RosalindThorpeGardens.example
Target Market(s)
Wholesale to Florists and Direct to Consumer via Farmers Market
Industry/Entity Type
Florist, Farm
Contact Information for Business Card
Name, Contact Info, Logo
Look and feel
Each slider illustrates characteristics of the customer's brand and the style your logo design should communicate.

```html
<!DOCTYPE html>
<html lang="en">
<head>
<meta charset="utf-8">
<title>Rosalind Thorpe Gardens – Business Card</title>
<link rel="stylesheet" href="https://fonts.googleapis.com/css2?family=Open+Sans:wght@400;600;700&display=swap">
<style>
  :root {
    --ink: #0c2b2f;
    --ink-deep: #071d20;
    --teal-glow: #2f7f8c;
    --paper: #ffffff;
    --stage: #e9ecec;
    --rule: #9aa5a6;
  }
  * { box-sizing: border-box; margin: 0; padding: 0; }
  html, body {
    width: 1200px; height: 900px; overflow: hidden;
    background: var(--stage);
    font-family: "Open Sans", Arial, sans-serif;
  }
  .canvas {
    width: 1200px; height: 900px;
    display: flex; flex-direction: column; align-items: center; justify-content: center;
    gap: 22px;
  }
  .card {
    width: 760px; height: 428px; position: relative; overflow: hidden;
    box-shadow: 0 6px 18px rgba(0,0,0,.18);
  }
  /* front */
  .card-front { background: var(--paper); }
  .front-swoosh { position: absolute; inset: 0; }
  .brand-seal {
    position: absolute; left: 70px; top: 44px;
    width: 170px; height: 170px; border-radius: 50%;
    border: 2px solid var(--ink);
    display: flex; align-items: center; justify-content: center; text-align: center;
    color: var(--ink); font-weight: 600; font-size: 19px; line-height: 1.25;
    letter-spacing: .04em; text-transform: uppercase; padding: 18px;
  }
  .divider {
    position: absolute; left: 272px; top: 44px; width: 1.5px; height: 200px;
    background: var(--rule);
  }
  .contact-block { position: absolute; left: 294px; top: 40px; color: var(--ink); }
  .holder-name { font-weight: 700; font-size: 34px; line-height: 1.1; }
  .holder-role { font-size: 16px; margin: 2px 0 12px; }
  .contact-list { list-style: none; }
  .contact-item {
    display: flex; align-items: center; gap: 10px;
    font-size: 19px; line-height: 1.55;
  }
  .contact-icon { width: 16px; height: 16px; flex: none; }
  /* back */
  .card-back {
    background: linear-gradient(160deg, var(--teal-glow) 0%, var(--ink) 35%, var(--ink-deep) 100%);
  }
  .back-pattern { position: absolute; inset: 0; }
  .back-brand {
    position: absolute; left: 0; right: 0; top: 50%; transform: translateY(-50%);
    text-align: center; color: var(--paper);
    font-weight: 600; font-size: 24px; letter-spacing: .08em; text-transform: uppercase;
  }
</style>
</head>
<body>
<main class="canvas">

  <section class="card card-front" aria-label="Business card front">
    <svg class="front-swoosh" viewBox="0 0 760 428" preserveAspectRatio="none" aria-hidden="true">
      <path d="M0 300 Q380 420 760 372 L760 428 L0 428 Z" fill="var(--ink)"/>
      <path d="M0 276 Q390 392 760 352" fill="none" stroke="var(--ink)" stroke-width="3"/>
    </svg>

    <div class="brand-seal">Rosalind Thorpe Gardens</div>
    <div class="divider"></div>

    <div class="contact-block">
      <h1 class="holder-name">Corinne Haldwick</h1>
      <p class="holder-role">Owner</p>
      <ul class="contact-list">
        <li class="contact-item">
          <svg class="contact-icon" viewBox="0 0 16 16" aria-hidden="true"><path d="M3.5 1.5l2.5 3-1.5 1.8a9 9 0 0 0 5.2 5.2L11.5 10l3 2.5-1.3 2.3C7 14.5 1.5 9 1.2 2.8z" fill="var(--ink)"/></svg>
          913-555-0147
        </li>
        <li class="contact-item">
          <svg class="contact-icon" viewBox="0 0 16 16" aria-hidden="true"><circle cx="8" cy="8" r="7" fill="var(--ink)"/></svg>
          Rosalind Thorpe Gardens
        </li>
        <li class="contact-item">
          <svg class="contact-icon" viewBox="0 0 16 16" aria-hidden="true"><circle cx="8" cy="8" r="7" fill="var(--ink)"/></svg>
          @RosalindThorpeGardens
        </li>
        <li class="contact-item">
          <svg class="contact-icon" viewBox="0 0 16 16" aria-hidden="true"><circle cx="8" cy="8" r="6.5" fill="none" stroke="var(--ink)" stroke-width="1.6"/><ellipse cx="8" cy="8" rx="3" ry="6.5" fill="none" stroke="var(--ink)" stroke-width="1.4"/><line x1="1.5" y1="8" x2="14.5" y2="8" stroke="var(--ink)" stroke-width="1.4"/></svg>
          www.RosalindThorpeGardens.example
        </li>
      </ul>
    </div>
  </section>

  <section class="card card-back" aria-label="Business card back">
    <svg class="back-pattern" viewBox="0 0 760 428" preserveAspectRatio="none" role="img" aria-label="Repeating glossy monogram pattern in dark teal">
      <defs>
        <linearGradient id="patternSheen" x1="0" y1="0" x2="1" y2="1">
          <stop offset="0" stop-color="#3f9aa8" stop-opacity=".35"/>
          <stop offset=".5" stop-color="#0c2b2f" stop-opacity="0"/>
          <stop offset="1" stop-color="#000" stop-opacity=".25"/>
        </linearGradient>
      </defs>
      <rect width="760" height="428" fill="url(#patternSheen)"/>
    </svg>
    <p class="back-brand">Rosalind Thorpe Gardens</p>
  </section>

</main>
</body>
</html>
```